Business card design for my company.
I would like the card's background colour to be black. You can also see our web site to get an idea of our brand. https://www.tmwhomecrafting.com.au/
- Name
- Email

```html
<!DOCTYPE html>
<html lang="en">
<head>
<meta charset="utf-8">
<title>TMW Home Crafting – Business Card</title>
<link rel="stylesheet" href="https://fonts.googleapis.com/css2?family=Montserrat:wght@400;500;600&display=swap">
<style>
  :root {
    --brand-green: #1f9a48;
    --brand-green-light: #7fc28c;
    --card-black: #111111;
    --ink-light: #e8e8ea;
    --stage: #5a5a5c;
    --shadow: rgba(0, 0, 0, 0.5);
  }
  * { box-sizing: border-box; margin: 0; padding: 0; }
  html, body {
    width: 1200px;
    height: 1153px;
    overflow: hidden;
    background: var(--stage);
    font-family: "Montserrat", sans-serif;
  }
  .card {
    position: absolute;
    left: 205px;
    width: 790px;
    height: 435px;
    overflow: hidden;
    background: var(--card-black);
    box-shadow: 0 10px 24px var(--shadow);
  }
  .card--front { top: 98px; }
  .card--back { top: 580px; }

  .front-shape { position: absolute; inset: 0; width: 100%; height: 100%; }

  .holder { position: absolute; left: 55px; top: 52px; color: #fff; }
  .holder__name { font-size: 31px; font-weight: 400; line-height: 1.1; }
  .holder__title { font-size: 15px; font-weight: 400; margin-top: 4px; }

  .contact {
    position: absolute;
    left: 48px;
    top: 330px;
    list-style: none;
    color: var(--ink-light);
    font-size: 17px;
  }
  .contact__item { display: flex; align-items: center; height: 22px; margin-bottom: 2px; }
  .contact__icon { width: 14px; height: 14px; margin-right: 14px; fill: var(--brand-green); }

  .wordmark { position: absolute; text-align: center; font-weight: 600; line-height: 1; color: var(--brand-green); }
  .wordmark--front { right: 38px; bottom: 60px; }
  .wordmark--front .wordmark__initials { font-size: 50px; letter-spacing: 2px; }
  .wordmark--front .wordmark__name { font-size: 11px; letter-spacing: 1.5px; margin-top: 6px; }

  .wordmark--back { left: 0; right: 0; top: 150px; }
  .wordmark--back .wordmark__initials { font-size: 112px; letter-spacing: 6px; }
  .wordmark--back .wordmark__name { font-size: 24px; letter-spacing: 3px; margin-top: 14px; }
</style>
</head>
<body>

<section class="card card--front" aria-label="Business card front">
  <svg class="front-shape" viewBox="0 0 790 435" preserveAspectRatio="none" aria-hidden="true">
    <rect width="790" height="435" fill="var(--brand-green)"/>
    <polygon points="0,245 540,18 790,210 790,435 0,435" fill="var(--brand-green-light)"/>
    <polygon points="0,272 545,24 790,192 790,435 0,435" fill="var(--card-black)"/>
  </svg>

  <div class="holder">
    <p class="holder__name">Dean Whitford</p>
    <p class="holder__title">General Manager</p>
  </div>

  <ul class="contact">
    <li class="contact__item">
      <svg class="contact__icon" viewBox="0 0 24 24" aria-hidden="true"><path d="M6.6 10.8a15.1 15.1 0 0 0 6.6 6.6l2.2-2.2a1 1 0 0 1 1-.25 11.4 11.4 0 0 0 3.6.57 1 1 0 0 1 1 1V20a1 1 0 0 1-1 1A17 17 0 0 1 3 4a1 1 0 0 1 1-1h3.5a1 1 0 0 1 1 1c0 1.25.2 2.45.57 3.57a1 1 0 0 1-.25 1z"/></svg>
      0400 555 123
    </li>
    <li class="contact__item">
      <svg class="contact__icon" viewBox="0 0 24 24" aria-hidden="true"><path d="M2 5h20v14H2z"/></svg>
      info@tmwhomecrafting.com.au
    </li>
    <li class="contact__item">
      <svg class="contact__icon" viewBox="0 0 24 24" aria-hidden="true"><path d="M12 2a7 7 0 0 0-7 7c0 5.2 7 13 7 13s7-7.8 7-13a7 7 0 0 0-7-7zm0 9.5A2.5 2.5 0 1 1 12 6.5a2.5 2.5 0 0 1 0 5z"/></svg>
      Riverton, Tasmania, Australia
    </li>
  </ul>

  <div class="wordmark wordmark--front">
    <p class="wordmark__initials">TMW</p>
    <p class="wordmark__name">HOME CRAFTING</p>
  </div>
</section>

<section class="card card--back" aria-label="Business card back">
  <div class="wordmark wordmark--back">
    <p class="wordmark__initials">TMW</p>
    <p class="wordmark__name">HOME CRAFTING</p>
  </div>
</section>

</body>
</html>
```